Book cover

I am working with my publisher to publish my book They came up with a book cover but I don't like it. I want to see different designs. The book Title is Brightwater the subtitle Ways to Guide Teams Through Storms with Poise, Purpose & Pace by Marlene T. Ostrowski
I want to use my Brand Colors including the blue. I am uploading the covers of my other book. This is a professional leadership book. The publisher will make the cover when providing them a new design. the Brightwater one is one I played with on Canva. I would like more color and to incorporate the blue. I want a spot at the top where I can write a quote. Brightwater is one word in the text so should be the same on the cover. I want the cover to show energy movement and am open to an image too. I am attaching logos for the feel of the brand and brand rgb codes.

```html
<!DOCTYPE html>
<html lang="en">
<head>
<meta charset="UTF-8">
<title>Brightwater — Book Cover</title>
<link rel="stylesheet" href="https://fonts.googleapis.com/css2?family=Antonio:wght@700&family=Oswald:wght@300&family=Montserrat:wght@600&display=swap">
<style>
  :root {
    --backdrop: #414042;
    --paper: #ffffff;
    --brand-blue: #0033a1;
    --brand-sky: #3d8fd6;
    --brand-mist: #eaf2fb;
    --brand-red: #ed1c24;
    --ink: #3a3a3c;
  }
  * { margin: 0; padding: 0; box-sizing: border-box; }
  html, body {
    width: 1200px;
    height: 1200px;
    overflow: hidden;
    background: var(--backdrop);
  }
  .canvas {
    position: relative;
    width: 1200px;
    height: 1200px;
    background: var(--backdrop);
  }
  .cover {
    position: absolute;
    left: 231px;
    top: 46px;
    width: 741px;
    height: 1110px;
    background: var(--paper);
    overflow: hidden;
  }
  .cover-art {
    position: absolute;
    inset: 0;
    width: 741px;
    height: 1110px;
  }
  .quote-band { fill: var(--brand-mist); }
  .quote-rule { fill: var(--brand-blue); }
  .title-text {
    font-family: "Antonio", "League Gothic", sans-serif;
    font-weight: 700;
    font-size: 238px;
  }
  .title-lead { fill: var(--brand-blue); }
  .title-tail { fill: var(--brand-red); }
  .accent-rule { fill: var(--brand-red); }
  .motion-line { fill: none; stroke-linecap: round; }
  .motion-blue { stroke: var(--brand-blue); }
  .motion-sky { stroke: var(--brand-sky); }
  .motion-red { stroke: var(--brand-red); }
  .visually-hidden {
    position: absolute; width: 1px; height: 1px;
    overflow: hidden; clip: rect(0 0 0 0);
  }
  .subtitle {
    position: absolute;
    right: 314px;
    top: 418px;
    text-align: right;
    font-family: "Oswald", "Barlow Condensed", sans-serif;
    font-weight: 300;
    font-size: 32px;
    line-height: 46px;
    color: var(--ink);
    letter-spacing: -0.3px;
  }
  .author {
    position: absolute;
    right: 314px;
    top: 1002px;
    text-align: right;
    font-family: "Montserrat", "Gotham", sans-serif;
    font-weight: 600;
    font-size: 29px;
    line-height: 40px;
    color: var(--ink);
  }
</style>
</head>
<body>
  <main class="canvas">
    <section class="cover" aria-label="Book cover: Brightwater by Marlene T. Ostrowski">
      <svg class="cover-art" viewBox="0 0 741 1110" xmlns="http://www.w3.org/2000/svg" aria-hidden="true">
        <rect class="quote-band" x="0" y="0" width="741" height="92"/>
        <rect class="quote-rule" x="0" y="92" width="741" height="4"/>

        <path class="motion-line motion-sky" stroke-width="6" d="M462 640 C 540 600, 600 700, 741 610"/>
        <path class="motion-line motion-blue" stroke-width="10" d="M462 700 C 550 650, 610 770, 741 680"/>
        <path class="motion-line motion-red" stroke-width="6" d="M462 760 C 560 720, 620 830, 741 750"/>
        <path class="motion-line motion-sky" stroke-width="3" d="M462 815 C 570 785, 630 880, 741 815"/>

        <rect class="accent-rule" x="441" y="290" width="21" height="820"/>
        <text class="title-text title-lead" x="31" y="316" textLength="372" lengthAdjust="spacingAndGlyphs">Bright</text>
        <text class="title-text title-tail" x="407" y="316" textLength="307" lengthAdjust="spacingAndGlyphs">water</text>
      </svg>

      <h1 class="visually-hidden">Brightwater</h1>

      <p class="subtitle">
        Ways to<br>
        Guide Teams Through<br>
        Storms with Poise,<br>
        Purpose &amp; Pace
      </p>

      <p class="author">
        Marlene<br>
        T. Ostrowski
      </p>
    </section>
  </main>
</body>
</html>
```